Letter design, envelope design, and more

Hello, we the Tavrin Gmbh are looking for our shop. Letter C5. Design does not have to be like a business card, so it can have straight lines. Only the color is important. The logo is the text under TaVRin omit.It should not be playful but Profesionel

Font styles to use
Sans Serif

Colors
0555a3
3176b5
85abd2
85cae6
34a7d8
0792cd
cee9f5
cfdfed
000000

Requirements
Must have
• Color like business card, Please, with the text under TaVRin, Correct address Lindmattstr. 4 Zip code 9517 Goldach, as well as Couvert Without addressing only design and logo with TaVrn
Nice to have
• more writing articles
Should not have
• Not too colored, Text under TaVRin, bright colors

```html
<!DOCTYPE html>
<html lang="en">
<head>
<meta charset="utf-8">
<title>TaVRin Gmbh – Letterhead</title>
<link href="https://fonts.googleapis.com/css2?family=Source+Sans+3:wght@400;600;700&display=swap" rel="stylesheet">
<style>
  :root{
    --navy:#001a70;
    --royal:#4163c0;
    --steel:#7aa7c4;
    --sky:#a9c7da;
    --ink:#111111;
    --paper:#ffffff;
    --backdrop:#e9edf2;
  }
  html,body{margin:0;padding:0;width:1200px;height:1006px;overflow:hidden;background:var(--backdrop);}
  body{font-family:"Source Sans 3",Arial,sans-serif;color:var(--ink);}
  .letter{position:absolute;left:302px;top:82px;width:595px;height:842px;background:var(--paper);overflow:hidden;}
  .header-art{position:absolute;left:0;top:0;}
  .brand{position:absolute;left:44px;top:40px;display:flex;align-items:center;gap:8px;}
  .brand-square{width:22px;height:22px;background:var(--navy);}
  .brand-name{font-size:31px;font-weight:700;color:var(--navy);letter-spacing:1px;line-height:1;}
  .website{position:absolute;left:414px;top:55px;color:#fff;font-size:13px;letter-spacing:2.4px;}
  .body-copy{position:absolute;left:88px;top:230px;width:425px;font-size:11.4px;line-height:12.7px;letter-spacing:-0.15px;}
  .salutation{font-size:12.2px;font-weight:600;margin:0 0 40px;}
  .body-copy p{margin:0 0 13px;}
  .signature{position:absolute;left:88px;top:547px;width:90px;height:46px;background:linear-gradient(90deg,#e8e8e8,#f4f4f4);}
  .signatory{position:absolute;left:88px;top:603px;font-size:12.2px;line-height:18px;}
  .footer-art{position:absolute;left:0;top:785px;}
  .contacts{position:absolute;left:220px;top:801px;display:flex;align-items:center;font-size:9.2px;color:var(--navy);white-space:nowrap;}
  .contact{display:flex;align-items:center;gap:3px;}
  .contact svg{width:10px;height:10px;}
  .contact.phone{width:107px;}
  .contact.email{width:106px;}
  .divider{display:inline-block;width:1px;height:14px;background:var(--navy);margin:0 3px;}
</style>
</head>
<body>
<main class="letter">
  <svg class="header-art" width="595" height="92" viewBox="0 0 595 92">
    <rect x="0" y="0" width="300" height="18" fill="var(--sky)"/>
    <path d="M278,0 H330 L356,92 H312 Q305,92 302,84 Z" fill="var(--steel)"/>
    <path d="M310,0 H340 L368,92 H336 Z" fill="var(--royal)"/>
    <path d="M338,0 H595 V92 H380 Q370,92 366,82 Z" fill="var(--navy)"/>
  </svg>
  <div class="brand"><span class="brand-square"></span><span class="brand-name">TaVRin</span></div>
  <div class="website">www.tavrin.ch</div>

  <section class="body-copy">
    <p class="salutation">Dear Mr. Weber,</p>
    <p>Lorem ipsum dolor sit amet, consectetur adipiscing elit. Cras elementum eget sem quis tincidunt. Suspendisse congue accumsan ipsum ac auctor.</p>
    <p>Fusce sagittis tellus a urna ornare eleifend. Interdum et malesuada fames ac ante ipsum primis in faucibu. Fusce pulvinar sodales diam et consequat. Praesent placerat nulla vitae nisl ullamcorper, vel facilisis lorem consequat. Fusce sagittis tellus a urna ornare eleifend. Interdum et malesuada fames ac ante ipsum primis in faucibu. Fusce pulvinar sodales diam et consequat. Praesent placerat nulla vitae nisl ullamcorper, vel facilisis lorem consequat.</p>
    <p>Fusce sagittis tellus a urna ornare eleifend. Interdum et malesuada fames ac ante ipsum primis in faucibu. Fusce pulvinar sodales diam et consequat. Praesent placerat nulla vitae nisl ullamcorper, vel facilisis lorem consequat.</p>
    <p>Lorem ipsum dolor sit amet, consectetur adipiscing elit. Cras elementum eget sem quis tincidunt.</p>
  </section>

  <div class="signature" role="img" aria-label="Handwritten signature"></div>
  <div class="signatory">Lukas Brenner<br>Co Founder &amp; CEO</div>

  <svg class="footer-art" width="595" height="57" viewBox="0 0 595 57">
    <rect x="190" y="38" width="405" height="19" fill="var(--sky)"/>
    <path d="M168,0 H182 Q187,0 189,6 L206,57 H188 Z" fill="var(--steel)"/>
    <path d="M147,0 H170 L190,57 H166 Z" fill="var(--royal)"/>
    <path d="M0,0 H150 L168,57 H0 Z" fill="var(--navy)"/>
  </svg>

  <div class="contacts">
    <span class="contact phone">
      <svg viewBox="0 0 10 10"><path d="M2,1 L3.5,1 L4.2,3 L3.2,3.8 Q4,5.8 6.2,6.8 L7,5.8 L9,6.5 L9,8 Q9,9 8,9 Q1,8.5 1,2 Q1,1 2,1 Z" fill="none" stroke="currentColor" stroke-width="0.8"/></svg>
      +41 71 555 01 23
    </span>
    <span class="contact email">
      <svg viewBox="0 0 10 10"><rect x="0.5" y="2" width="9" height="6" fill="none" stroke="currentColor" stroke-width="0.8"/><path d="M0.5,2 L5,5.5 L9.5,2" fill="none" stroke="currentColor" stroke-width="0.8"/></svg>
      info@tavrin.ch
    </span>
    <span class="contact address">
      <svg viewBox="0 0 10 10"><path d="M5,9.5 Q1.5,5.5 1.5,3.8 A3.5,3.5 0 0 1 8.5,3.8 Q8.5,5.5 5,9.5 Z" fill="none" stroke="currentColor" stroke-width="0.8"/><circle cx="5" cy="3.8" r="1.2" fill="none" stroke="currentColor" stroke-width="0.8"/></svg>
      Lindmattstr. 4<span class="divider"></span>9517 Goldach
    </span>
  </div>
</main>
</body>
</html>
```